Modern looking signage for dental office.

Exterior signage for passing cars
Updates
Need extra days to review
Target Market(s)
Cars passing by
Font styles to use
Sans Serif
Colors
3276b5
Requirements
Must have
- Logo
- OPEN ON SUTURDAY AND SUNDAY
- NIGHT CLINIC AVAILABLE
- PLEASE USE THE FONT TYPE IN FILE 4 UPLOADED BELOW.
- (847) 302-7469
- Modern looking

```html
<!DOCTYPE html>
<html lang="en">
<head>
<meta charset="utf-8">
<title>Bright Arc Dental – Weekend Night Clinic Sign</title>
<link rel="stylesheet" href="https://fonts.googleapis.com/css2?family=Open+Sans:wght@400;600;700;800&display=swap">
<style>
  :root {
    --page: #ececec;
    --sign: #ffffff;
    --teal: #17869d;
    --teal-deep: #0f6f84;
    --teal-light: #3aa5ba;
    --red: #e11d25;
    --ink: #454545;
    --grey: #5f5f5f;
    --rule: #b9b9b9;
    --swoosh: #d6d6d6;
    --photo-a: #3c4a63;
    --photo-b: #1f2a3d;
  }
  * { margin: 0; padding: 0; box-sizing: border-box; }
  html, body {
    width: 1200px; height: 2311px; overflow: hidden;
    background: var(--page);
    font-family: "Open Sans", Arial, sans-serif;
  }
  .sign {
    position: absolute; left: 50px; top: 605px;
    width: 1100px; height: 1100px;
    background: var(--sign);
    overflow: hidden;
    box-shadow: 0 10px 30px rgba(0,0,0,.18);
  }
  .brand { position: absolute; left: 191px; top: 64px; display: flex; align-items: center; }
  .brand-mark {
    width: 151px; height: 151px; border-radius: 50%;
    border: 3px solid var(--ink); flex: none;
  }
  .brand-text { margin-left: 20px; }
  .brand-name {
    font-size: 54px; font-weight: 400; color: var(--ink);
    letter-spacing: 1px; line-height: 1.1; white-space: nowrap;
  }
  .brand-tagline {
    font-size: 28px; font-weight: 400; color: var(--ink);
    letter-spacing: .3px; margin-top: 6px; white-space: nowrap;
  }
  .center-line {
    position: absolute; left: 0; width: 100%; text-align: center;
    transform: translateY(-50%); white-space: nowrap; line-height: 1.2;
  }
  .open-on { top: 325px; font-size: 78px; font-weight: 800; color: var(--red); }
  .days-band {
    position: absolute; left: 65px; top: 372px; width: 992px; height: 100px;
    border-radius: 50px;
    background: linear-gradient(180deg, var(--teal-light) 0%, var(--teal) 45%, var(--teal-deep) 100%);
    box-shadow: 0 12px 14px -10px rgba(0,0,0,.45);
    display: flex; align-items: center; justify-content: center;
    font-size: 74px; font-weight: 800; color: #fff; letter-spacing: .5px; white-space: nowrap;
  }
  .night-from { top: 535px; font-size: 47px; font-weight: 600; color: var(--grey); }
  .rule { position: absolute; left: 235px; width: 625px; height: 2px; background: var(--rule); }
  .rule-top { top: 567px; }
  .rule-bottom { top: 667px; }
  .hours { top: 617px; font-size: 86px; font-weight: 800; color: var(--teal); }
  .available { top: 703px; font-size: 47px; font-weight: 700; color: var(--grey); }
  .wave { position: absolute; left: 0; top: 0; width: 1100px; height: 1100px; }
  .dentist-photo {
    position: absolute; left: 0; top: 690px; width: 345px; height: 410px;
    background: linear-gradient(180deg, var(--photo-a), var(--photo-b));
  }
  .call-line {
    position: absolute; right: 86px; text-align: right; color: #fff;
    font-weight: 800; line-height: 1.2; white-space: nowrap; transform: translateY(-50%);
  }
  .call-label { top: 913px; font-size: 95px; }
  .call-number { top: 1014px; font-size: 84px; }
</style>
</head>
<body>
  <main class="sign">
    <div class="brand">
      <div class="brand-mark"></div>
      <div class="brand-text">
        <div class="brand-name">BRIGHT ARC DENTAL</div>
        <div class="brand-tagline">MODERN GENERAL DENTISTRY</div>
      </div>
    </div>

    <div class="center-line open-on">OPEN ON</div>
    <div class="days-band">SATURDAY &amp; SUNDAY</div>
    <div class="center-line night-from">NIGHT CLINIC FROM</div>
    <div class="rule rule-top"></div>
    <div class="center-line hours">5PM TO 10PM</div>
    <div class="rule rule-bottom"></div>
    <div class="center-line available">AVAILABLE</div>

    <svg class="wave" viewBox="0 0 1100 1100" aria-hidden="true">
      <path fill="var(--swoosh)" d="M0,790 C200,880 420,890 650,790 C830,715 980,720 1100,732 L1100,772 C980,760 850,750 650,830 C400,930 200,930 0,860 Z"/>
      <path fill="var(--teal)" d="M0,860 C200,930 400,930 650,830 C850,750 980,760 1100,772 L1100,1100 L0,1100 Z"/>
    </svg>

    <div class="dentist-photo" role="img" aria-label="Photo of the smiling dentist in navy scrubs with dental loupes"></div>

    <div class="call-line call-label">Call Us</div>
    <div class="call-line call-number">(847) 302-7469</div>
  </main>
</body>
</html>
```